Business card for Luxury Portable Restroom Trailer company

We are a Luxury Portable Restroom Trailer Company Called FALCRIDGE HIRES. Based in Orange County California. We provide portable restroom trailers for events, such as, Weddings, Concerts, Charity events, Sporting events, Tournaments, Corporate events, ect. We rent and Sell the Luxury restrooms. Our colors are white, grey, and Orange. As you will see in the logo we uploaded.
There are 2 people in the company so the names and titles will change for the 3 people but card will remain the same. Here is the information for each Person: Dwight Penner CFO 555 318-0476
next Person: Leon Marchetti VP 555 318-0476
Next Person: Owen Marchetti CEO 555 318-0476
Information to include on the card: Luxury Restroom Trailers Rental and Sales. Weddings, Concerts, Charity, Sporting and Corp. Events.

```html
<!DOCTYPE html>
<html lang="en">
<head>
<meta charset="utf-8">
<title>Falcridge Hires – Business Card</title>
<link rel="stylesheet" href="https://fonts.googleapis.com/css2?family=Montserrat:wght@400;500;700;800&display=swap">
<style>
  :root {
    --bg: #1d1d20;
    --card-grey: #5a5a5c;
    --card-orange: #f26b21;
    --ink-light: #ffffff;
    --ink-dark: #2f241e;
    --rule: #4a3a30;
  }
  * { box-sizing: border-box; margin: 0; padding: 0; }
  html, body {
    width: 1200px; height: 900px; overflow: hidden;
    background: var(--bg);
    font-family: "Montserrat", sans-serif;
  }
  .canvas { position: relative; width: 1200px; height: 900px; }
  .card {
    position: absolute; left: 250px; width: 700px; height: 400px;
    border-radius: 22px;
  }
  .card--front { top: 35px; background: var(--card-grey); }
  .card--back  { top: 465px; background: var(--card-orange); }

  .wordmark {
    position: absolute; display: flex; align-items: center;
    color: var(--ink-light); font-weight: 800;
  }
  .wordmark__square { background: var(--ink-light); flex: none; }
  .wordmark__text { display: flex; flex-direction: column; line-height: 1; }
  .wordmark__main { letter-spacing: 0.02em; }
  .wordmark__sub { letter-spacing: 0.32em; align-self: flex-end; }

  .card--front .wordmark { left: 50%; top: 50%; transform: translate(-50%, -50%); gap: 22px; }
  .card--front .wordmark__square { width: 54px; height: 54px; }
  .card--front .wordmark__main { font-size: 66px; }
  .card--front .wordmark__sub { font-size: 28px; margin-top: 10px; }

  .card--back .wordmark { left: 48px; top: 230px; gap: 10px; }
  .card--back .wordmark__square { width: 22px; height: 22px; }
  .card--back .wordmark__main { font-size: 28px; }
  .card--back .wordmark__sub { font-size: 12px; margin-top: 5px; }

  .divider {
    position: absolute; left: 352px; top: 70px; width: 1.5px; height: 260px;
    background: var(--rule);
  }
  .contact { position: absolute; left: 380px; top: 78px; color: var(--ink-dark); }
  .contact__name { color: var(--ink-light); font-weight: 700; font-size: 26px; }
  .contact__title { font-size: 14px; font-weight: 500; margin-top: 2px; }
  .contact__address { font-size: 14px; line-height: 1.35; margin-top: 18px; }
  .contact__list { list-style: none; margin-top: 18px; font-size: 14px; }
  .contact__list li { display: flex; align-items: center; gap: 10px; line-height: 1.55; }
  .contact__list svg { width: 13px; height: 13px; flex: none; fill: var(--ink-light); }
</style>
</head>
<body>
<main class="canvas">
  <section class="card card--front" aria-label="Card front">
    <div class="wordmark">
      <span class="wordmark__square"></span>
      <span class="wordmark__text">
        <span class="wordmark__main">FALCRIDGE</span>
        <span class="wordmark__sub">HIRES</span>
      </span>
    </div>
  </section>

  <section class="card card--back" aria-label="Card back">
    <div class="wordmark">
      <span class="wordmark__square"></span>
      <span class="wordmark__text">
        <span class="wordmark__main">FALCRIDGE</span>
        <span class="wordmark__sub">HIRES</span>
      </span>
    </div>

    <div class="divider"></div>

    <div class="contact">
      <p class="contact__name">Owen Marchetti</p>
      <p class="contact__title">CEO</p>
      <p class="contact__address">418 Harbor Crest Ave. #112<br>Tustin, CA 92780</p>
      <ul class="contact__list">
        <li>
          <svg viewBox="0 0 16 16" aria-hidden="true"><path d="M3 1h3l1.5 4-2 1.3a9 9 0 0 0 4.2 4.2L11 8.5l4 1.5v3a2 2 0 0 1-2 2A12 12 0 0 1 1 3a2 2 0 0 1 2-2z"/></svg>
          555 318-0476
        </li>
        <li>
          <svg viewBox="0 0 16 16" aria-hidden="true"><path d="M4 0h8a1 1 0 0 1 1 1v14a1 1 0 0 1-1 1H4a1 1 0 0 1-1-1V1a1 1 0 0 1 1-1zm1 2v10h6V2zm3 11a1 1 0 1 0 0 2 1 1 0 0 0 0-2z"/></svg>
          555 318-0476
        </li>
        <li>
          <svg viewBox="0 0 16 16" aria-hidden="true"><path d="M0 3h16v10H0zm1.5 1.2v.3L8 9l6.5-4.5v-.3z"/></svg>
          info@falcridgehires.com
        </li>
        <li>
          <svg viewBox="0 0 16 16" aria-hidden="true"><circle cx="8" cy="8" r="7.5"/></svg>
          www.falcridgehires.com
        </li>
      </ul>
    </div>
  </section>
</main>
</body>
</html>
```